Boutique custom software development company needs new business card

Our nearly 20 year old custom software development company would like to better include the fact that we are now providing Bitcoin services. These new services are B2B include education (how to acquire and securely hold Bitcoin) and integrating Bitcoin payments into existing ecommerce sites or other existing systems. Please keep the card clean and simple. Attached is our current design and some other files. vextorial.com

Target Market(s)

businesses owners interested in long term relationship

Industry/Entity Type

Custom software development and Bitcoin

Contact Information for Business Card

Dale Parker, dale@vextorial.com, vextorial.com, (888) 555-VXTRL

Font styles to use
Other font styles liked:
• monospace

Requirements
Must have
• double-sided
Nice to have
• clean and simple
Should not have
• physical address

```html
<!DOCTYPE html>
<html lang="en">
<head>
<meta charset="utf-8">
<title>Vextorial — Business Card</title>
<link rel="stylesheet" href="https://fonts.googleapis.com/css2?family=Montserrat:wght@400;500;800&display=swap">
<style>
  :root {
    --backdrop: #c9c9c9;
    --brand-blue: #3d72bb;
    --brand-orange: #ef7f26;
    --paper: #ffffff;
    --ink: #3a3a3a;
    --card-shadow: 0 14px 28px rgba(0,0,0,0.28);
  }
  * { box-sizing: border-box; margin: 0; padding: 0; }
  html, body {
    width: 1200px; height: 900px; overflow: hidden;
    background: var(--backdrop);
    font-family: "Montserrat", sans-serif;
  }
  .canvas { position: relative; width: 1200px; height: 900px; }

  .card {
    position: absolute;
    width: 560px; height: 320px;
    border-radius: 30px;
    box-shadow: var(--card-shadow);
    overflow: hidden;
  }

  /* Front side */
  .card-front {
    left: 90px; top: 80px;
    background: linear-gradient(25deg, var(--brand-blue) 20%, #8a7a86 58%, var(--brand-orange) 100%);
    display: flex; flex-direction: column; align-items: center; justify-content: center;
    color: var(--paper);
  }
  .front-name {
    font-weight: 800; font-size: 62px; letter-spacing: 1px; text-transform: uppercase;
    line-height: 1;
  }
  .front-tagline {
    font-weight: 400; font-size: 21px; margin-top: 8px; letter-spacing: 0.3px;
  }

  /* Back side */
  .card-back {
    left: 550px; top: 500px;
    background: var(--paper);
  }
  .back-brand { position: absolute; left: 44px; top: 44px; color: var(--brand-blue); }
  .back-name {
    font-weight: 800; font-size: 40px; text-transform: uppercase; line-height: 1; letter-spacing: 0.5px;
  }
  .back-tagline { font-weight: 400; font-size: 14px; margin-top: 5px; }

  .person {
    position: absolute; left: 44px; top: 150px;
    font-weight: 800; font-size: 26px; text-transform: uppercase; letter-spacing: 0.5px;
  }
  .person-first { color: var(--brand-orange); }
  .person-last { color: var(--brand-blue); }

  .contact-list { position: absolute; left: 44px; top: 204px; list-style: none; }
  .contact-item {
    display: flex; align-items: center; gap: 12px;
    font-size: 17px; font-weight: 400; color: var(--ink); letter-spacing: 0.5px;
    margin-bottom: 8px;
  }
  .contact-icon {
    width: 24px; height: 24px; border-radius: 4px; background: var(--brand-orange);
    display: flex; align-items: center; justify-content: center; flex: none;
  }
  .website {
    position: absolute; right: 40px; top: 70px;
    font-size: 16px; font-weight: 500; color: var(--brand-blue); letter-spacing: 0.4px;
  }
  .website-domain { color: var(--brand-orange); }
</style>
</head>
<body>
<main class="canvas">

  <section class="card card-front" aria-label="Card front">
    <h1 class="front-name">Vextorial</h1>
    <p class="front-tagline">developer of custom applications</p>
  </section>

  <section class="card card-back" aria-label="Card back">
    <div class="back-brand">
      <p class="back-name">Vextorial</p>
      <p class="back-tagline">developer of custom applications</p>
    </div>

    <p class="website">www.<span class="website-domain">vextorial</span>.com</p>

    <h2 class="person"><span class="person-first">Dale</span> <span class="person-last">Parker</span></h2>

    <ul class="contact-list">
      <li class="contact-item">
        <span class="contact-icon">
          <svg width="14" height="14" viewBox="0 0 24 24" aria-hidden="true">
            <path fill="#fff" d="M6.6 10.8a15.1 15.1 0 0 0 6.6 6.6l2.2-2.2a1 1 0 0 1 1-.25 11.4 11.4 0 0 0 3.6.57 1 1 0 0 1 1 1V20a1 1 0 0 1-1 1A17 17 0 0 1 3 4a1 1 0 0 1 1-1h3.5a1 1 0 0 1 1 1c0 1.25.2 2.45.57 3.57a1 1 0 0 1-.25 1z"/>
          </svg>
        </span>
        (888) 555-VXTRL
      </li>
      <li class="contact-item">
        <span class="contact-icon">
          <svg width="15" height="15" viewBox="0 0 24 24" aria-hidden="true">
            <rect x="3" y="6" width="18" height="12" rx="1" fill="none" stroke="#fff" stroke-width="2"/>
            <path d="M3 7l9 6 9-6" fill="none" stroke="#fff" stroke-width="2"/>
          </svg>
        </span>
        dale@vextorial.com
      </li>
    </ul>
  </section>

</main>
</body>
</html>
```